Wordpress - For IT, Cloud/Hosting, Residential/Commercial Construction Services

We are a holding company for service companies. We want the current Wordpress site modified or a new wordpress site completed. We want this site to be the parent website, that then has pull down menus linking to our other website (currently http://brightwallfix.com, http://q7v.host and would like it to be easy and fluid as we acquire more companies as we have with TKLS, Inc., B&J Construction, Brightwall Fix etc. Model after sites like Pemrose.com, Tallowbine.com, QDV.com,.vanterelm.com

------

The parent is the main site q7v Corp. Below that are sub corps and DBAs. q7v Corp stands for Quick 7 Venture Corp. q7v Offers IT manages services, 24x7 support, Monitoring NOC, Remote Hands, Onsite support services. We have acquired TKLS, Inc, B & J Construction, BrightwallFix.com. We plan to acquire/spin up many companies that offer service, support and installation offerings and will all be known as an q7v Corp Company for branding purposes. We recently had our logo done, but then ran it through 3d glass as we like the look better than the original works. We have original files in vector, but not the 3D galss door render.

Target Market(s)

IT Server and Desktop Support. Construction. Mold Remediation. Mergers and Acquisitions.

Industry/Entity Type

It Company

Coding

Coded - Design and coding required

Font styles to use
Sans Serif

Colors
0792cd

Requirements
Must have
• Clean interface. Modern design. Mobile device and multi browser support. Must be for Wordpress. Job posting with resume submission module.Hook to our Web hosting portal (Tormund) API into VexaLine Reseller portal, customer portal to allow payments to their account etc.. Easy to edit. Easy to add to, Press Release Section, Investor Relations etc.
Should not have
• Slow loading. Played out design. Over use of stock images. Copied from a competitor or something point to such.

```html
<!DOCTYPE html>
<html lang="en">
<head>
<meta charset="utf-8">
<title>Q7V Corp</title>
<link rel="stylesheet" href="https://fonts.googleapis.com/css2?family=Raleway:wght@500;600;700;800&family=Open+Sans:ital,wght@0,400;0,600;0,700;1,400&display=swap">
<style>
:root{
  --brand:#0792cd;
  --brand-dark:#0a5f9e;
  --ink:#1d1d1d;
  --muted:#6a6a6a;
  --card:#f4f4f4;
  --line:#3a3a3a;
  --white:#ffffff;
  --star:#ffd81a;
  --icon:#1b87c9;
}
*{box-sizing:border-box;margin:0;padding:0}
html,body{width:1200px;height:3371px;overflow:hidden;background:var(--white)}
body{position:relative;font-family:'Open Sans',sans-serif;color:var(--ink)}
.abs{position:absolute}
.center{text-align:center}

/* hero */
.hero{left:0;top:0;width:1200px;height:627px;background:linear-gradient(180deg,#2b3644 0%,#3d4a5a 40%,#27303b 100%)}
.hero-photo{position:absolute;inset:0;background:radial-gradient(ellipse at 40% 50%,rgba(120,140,165,.45),rgba(20,26,34,.2) 70%)}
.brand{left:112px;top:58px;display:flex;align-items:center;gap:10px;color:var(--white);font-family:'Raleway',sans-serif;font-weight:700;font-size:24px;line-height:1}
.brand .dot{width:14px;height:14px;border-radius:50%;background:var(--white)}
.nav{top:64px;left:0;width:1200px;font-family:'Raleway',sans-serif;font-weight:700;font-size:15px;color:var(--white)}
.nav span{position:absolute}
.nav .active{color:var(--brand)}
.dropdown{left:577px;top:94px;width:284px;height:79px;background:var(--white);font-size:14px;color:#333}
.dropdown span{position:absolute}
.hero-title{top:200px;width:1200px;font-family:'Raleway',sans-serif;font-weight:800;font-size:90px;color:var(--white)}
.hero-sub{top:318px;width:1200px;font-size:27px;color:var(--white)}
.hero-btn{left:501px;top:395px;width:198px;height:59px;border:2px solid var(--white);border-radius:30px;color:var(--white);font-family:'Raleway',sans-serif;font-weight:700;font-size:15px;line-height:55px}
.dots{top:537px;left:564px}

/* welcome */
.h2{width:1200px;font-family:'Raleway',sans-serif;font-weight:700;font-size:34px;color:var(--ink)}
.lead{left:231px;top:776px;width:742px;font-size:14px;line-height:29px;color:var(--muted)}
.service{width:254px;text-align:center}
.service .ring{width:140px;height:140px;border:2px solid var(--line);border-radius:50%;margin:0 auto;display:flex;align-items:center;justify-content:center}
.service h3{font-family:'Raleway',sans-serif;font-weight:700;font-size:21px;margin-top:32px}
.service p{font-size:14px;line-height:27px;color:var(--muted);margin-top:8px}

/* about */
.about-photo{left:0;top:1272px;width:1200px;height:539px;background:linear-gradient(120deg,#b9b4ad 0%,#d6d3cf 40%,#8d9196 70%,#4b5058 100%)}
.about-box{left:112px;top:1344px;width:445px;height:397px;background:var(--white);text-align:center;padding-top:46px}
.about-box h2{font-family:'Raleway',sans-serif;font-weight:700;font-size:34px}
.about-box p{font-size:13.5px;line-height:27.5px;color:#444;margin:20px 22px 0}
.btn{display:inline-block;background:var(--brand-dark);color:var(--white);border-radius:26px;font-family:'Raleway',sans-serif;font-weight:700;font-size:15px}
.about-box .btn{width:139px;height:49px;line-height:49px;margin-top:26px}

/* blog */
.post{top:2000px;width:310px;height:445px}
.post .thumb{height:238px}
.post .body{position:absolute;left:12px;top:213px;width:286px;height:232px;background:var(--card);text-align:center;padding-top:22px}
.post h3{font-weight:600;font-size:22px}
.post .meta{font-size:14px;color:#444;margin-top:6px}
.post .meta svg{vertical-align:-2px;margin-right:3px}
.post p{font-size:14px;line-height:24px;color:var(--muted);margin:14px 18px 0}
.post .more{font-family:'Raleway',sans-serif;font-weight:700;font-size:14px;color:var(--brand-dark);margin-top:18px}

/* testimonials */
.band{left:0;top:2528px;width:1200px;height:505px;background:linear-gradient(135deg,#1680c6 0%,#0f6db1 55%,#0d63a4 100%)}
.band h2{position:absolute;top:72px;width:1200px;text-align:center;font-family:'Raleway',sans-serif;font-weight:700;font-size:34px;color:var(--white)}
.quote{top:2714px;width:306px;height:250px;border:2px solid var(--white);text-align:center;color:var(--white);padding-top:48px}
.quote p{font-style:italic;font-size:13px;line-height:26px;margin:0 24px}
.quote h4{font-weight:600;font-size:19px;margin-top:8px}
.avatar{top:2674px;width:86px;height:86px;border-radius:50%;border:3px solid var(--white);background:linear-gradient(180deg,#c9b6a4,#8a7768)}
.stars{margin-top:10px}
.arrow{top:2813px;width:48px;height:48px;border:2px solid rgba(255,255,255,.8);border-radius:50%}

/* footer */
.social{top:3145px;width:52px;height:52px;border:1.5px solid #555;border-radius:50%;font-size:11px;font-weight:600;color:var(--icon);line-height:49px;text-align:center}
.foot{width:1200px;text-align:center;font-size:14px;color:#333}
.foot .sep{margin:0 12px}
.foot svg{vertical-align:-2px;margin-right:6px}
</style>
</head>
<body>

<header class="abs hero">
  <div class="hero-photo" role="img" aria-label="Dim server racks in a data centre with blinking indicator lights"></div>
  <div class="abs brand"><span class="dot"></span>Q7V Corp</div>
  <nav class="abs nav">
    <span class="active" style="left:480px">HOME</span>
    <span style="left:575px">COMPANIES <svg width="10" height="8" viewBox="0 0 10 8"><path d="M0 1h10L5 7z" fill="#fff"/></svg></span>
    <span style="left:736px">SERVICES</span>
    <span style="left:859px">BLOG</span>
    <span style="left:951px">CONTACT</span>
    <span style="left:1073px;top:1px"><svg width="16" height="16" viewBox="0 0 16 16"><circle cx="6.5" cy="6.5" r="5" fill="none" stroke="#fff" stroke-width="2.2"/><path d="M10.5 10.5L15 15" stroke="#fff" stroke-width="2.5"/></svg></span>
  </nav>
  <div class="abs dropdown">
    <span style="left:19px;top:16px">Brightwall Fix</span>
    <span style="left:143px;top:16px">TKLS, Inc</span>
    <span style="left:19px;top:44px">q7v</span>
    <span style="left:143px;top:44px">B&amp;J Construction</span>
  </div>
  <h1 class="abs hero-title center">Q7V CORP</h1>
  <p class="abs hero-sub center">We are a holding company for various service companies</p>
  <div class="abs hero-btn center">GET MORE INFO</div>
  <svg class="abs dots" width="72" height="14" viewBox="0 0 72 14">
    <circle cx="7" cy="7" r="6" fill="#fff"/>
    <circle cx="25" cy="7" r="5.5" fill="none" stroke="#fff" stroke-width="1.5"/>
    <circle cx="43" cy="7" r="5.5" fill="none" stroke="#fff" stroke-width="1.5"/>
    <circle cx="61" cy="7" r="5.5" fill="none" stroke="#fff" stroke-width="1.5"/>
  </svg>
</header>

<section>
  <h2 class="abs h2 center" style="top:706px">WELCOME TO Q7V CORP</h2>
  <p class="abs lead center">Nemo enim ipsam voluptatem quia voluptas sit aspernatur aut odit aut fugit, sed quia consequuntur magni dolores eos qui ratione voluptatem sequi nesciunt. Neque porro quisquam est, qui dolorem ipsum quia dolor sit amet, consect etur, adipisci velit, sed quia non numquam eius modi tempora incidunt ut labore et.</p>

  <div class="abs service" style="left:91px;top:912px">
    <div class="ring"><svg width="58" height="48" viewBox="0 0 58 48"><path d="M6 6h30a5 5 0 015 5v14a5 5 0 01-5 5H18l-9 8v-8H6a5 5 0 01-5-5V11a5 5 0 015-5z" fill="none" stroke="#1b87c9" stroke-width="4"/><path d="M44 16h7a5 5 0 015 5v13a5 5 0 01-5 5h-2v7l-8-7H26a5 5 0 01-4-2" fill="#1b87c9"/></svg></div>
    <h3>IT consulting</h3>
    <p>Nemo enim ipsam voluptate quia voluptas sit aaspernatur.</p>
  </div>
  <div class="abs service" style="left:345px;top:912px">
    <div class="ring"><svg width="58" height="40" viewBox="0 0 58 40"><path d="M14 38a12 12 0 01-2-24 16 16 0 0130-4 13 13 0 0116 12 13 13 0 01-13 16z" fill="#1b87c9"/></svg></div>
    <h3>Cloud/Hosting</h3>
    <p>Nemo enim ipsam voluptate quia voluptas sit aaspernatur.</p>
  </div>
  <div class="abs service" style="left:599px;top:912px">
    <div class="ring"><svg width="52" height="44" viewBox="0 0 52 44"><path d="M18 8V4h16v4" fill="none" stroke="#1b87c9" stroke-width="4"/><rect x="1" y="9" width="50" height="34" rx="4" fill="#1b87c9"/><path d="M12 9v34M40 9v34" stroke="#fff" stroke-width="2"/></svg></div>
    <h3>Home/Commercial</h3>
    <p>Nemo enim ipsam voluptate quia voluptas sit aaspernatur.</p>
  </div>
  <div class="abs service" style="left:855px;top:912px">
    <div class="ring"><svg width="40" height="50" viewBox="0 0 40 50"><rect x="2" y="2" width="36" height="46" fill="none" stroke="#1b87c9" stroke-width="3.5"/><g fill="#1b87c9"><rect x="9" y="9" width="6" height="5"/><rect x="17" y="9" width="6" height="5"/><rect x="25" y="9" width="6" height="5"/><rect x="9" y="18" width="6" height="5"/><rect x="17" y="18" width="6" height="5"/><rect x="25" y="18" width="6" height="5"/><rect x="9" y="27" width="6" height="5"/><rect x="17" y="27" width="6" height="5"/><rect x="25" y="27" width="6" height="5"/><rect x="16" y="36" width="8" height="12"/></g></svg></div>
    <h3>Construction Services</h3>
    <p>Nemo enim ipsam voluptate quia voluptas sit aaspernatur.</p>
  </div>
</section>

<section>
  <div class="abs about-photo" role="img" aria-label="Desk with a laptop, phone and a tablet showing a circuit layout"></div>
  <div class="abs about-box">
    <h2>ABOUT Q7V CORP</h2>
    <p>q7v Corp is a Civeron and Tallowbine IT Solution Provider. We provide support for Desktops, Laptops, Tablets, Mobile Devices, Networking, WiFi, Server, Design and more by providing Remote and OnSite Support Services. q7v Corp (Quick 7 Venture) Full service one stop shop service provider. Our CEO and Founder Reed Calloway.</p>
    <span class="btn">READ MORE</span>
  </div>
</section>

<section>
  <h2 class="abs h2 center" style="top:1908px">LATEST BLOG</h2>

  <article class="abs post" style="left:112px">
    <div class="thumb" role="img" aria-label="Engineers working in front of a glowing network display" style="background:linear-gradient(135deg,#1c2a44,#3d6ea8 60%,#0f1a2e)"></div>
    <div class="body">
      <h3>Finibus Bonoruet Ma</h3>
      <div class="meta"><svg width="12" height="12" viewBox="0 0 12 12"><rect x="1" y="2" width="10" height="9" fill="#1b87c9"/></svg>18/06/2018 &nbsp;| &nbsp;<svg width="11" height="12" viewBox="0 0 11 12"><circle cx="5.5" cy="3.5" r="3" fill="#1b87c9"/><path d="M0 12a5.5 5 0 0111 0z" fill="#1b87c9"/></svg>Sam Ortell</div>
      <p>Nam libero tempore, cum soluta no bis est eligendi optio cumque nihil imp edit quo minus id quod maxi</p>
      <div class="more">READ MORE</div>
    </div>
  </article>

  <article class="abs post" style="left:445px">
    <div class="thumb" role="img" aria-label="Hand holding a smartphone in front of a laptop" style="background:linear-gradient(135deg,#2b1d14,#9a8a78 50%,#d8d2c8)"></div>
    <div class="body">
      <h3>Finibus Bonoruet Ma</h3>
      <div class="meta"><svg width="12" height="12" viewBox="0 0 12 12"><rect x="1" y="2" width="10" height="9" fill="#1b87c9"/></svg>18/06/2018 &nbsp;| &nbsp;<svg width="11" height="12" viewBox="0 0 11 12"><circle cx="5.5" cy="3.5" r="3" fill="#1b87c9"/><path d="M0 12a5.5 5 0 0111 0z" fill="#1b87c9"/></svg>Sam Ortell</div>
      <p>Nam libero tempore, cum soluta no bis est eligendi optio cumque nihil imp edit quo minus id quod maxi</p>
      <div class="more">READ MORE</div>
    </div>
  </article>

  <article class="abs post" style="left:777px">
    <div class="thumb" role="img" aria-label="Looking up at glass towers with sunlight and clouds" style="background:linear-gradient(160deg,#6b7f95,#e8d6b0 45%,#aab7c6 70%,#5d6b7b)"></div>
    <div class="body">
      <h3>Finibus Bonoruet Ma</h3>
      <div class="meta"><svg width="12" height="12" viewBox="0 0 12 12"><rect x="1" y="2" width="10" height="9" fill="#1b87c9"/></svg>18/06/2018 &nbsp;| &nbsp;<svg width="11" height="12" viewBox="0 0 11 12"><circle cx="5.5" cy="3.5" r="3" fill="#1b87c9"/><path d="M0 12a5.5 5 0 0111 0z" fill="#1b87c9"/></svg>Sam Ortell</div>
      <p>Nam libero tempore, cum soluta no bis est eligendi optio cumque nihil imp edit quo minus id quod maxi</p>
      <div class="more">READ MORE</div>
    </div>
  </article>
</section>

<section>
  <div class="abs band"><h2>TESTIMONIALS</h2></div>

  <div class="abs quote" style="left:112px"><p>Nam libero tempore, cum soluta nobis est eligendi optio cumque nihil impedit quo minus id quod maxime placea</p><h4>Nora Vantell</h4>
    <svg class="stars" width="90" height="16" viewBox="0 0 90 16"><g fill="#ffd81a"><path id="st" d="M8 0l2.4 5 5.6.6-4.2 3.8 1.2 5.6L8 12.2 3 15l1.2-5.6L0 5.6 5.6 5z"/><use href="#st" x="18"/><use href="#st" x="36"/><use href="#st" x="54"/><use href="#st" x="72"/></g></svg></div>
  <div class="abs quote" style="left:447px"><p>Nam libero tempore, cum soluta nobis est eligendi optio cumque nihil impedit quo minus id quod maxime placea</p><h4>Tessa Morrow</h4>
    <svg class="stars" width="90" height="16" viewBox="0 0 90 16"><g fill="#ffd81a"><use href="#st"/><use href="#st" x="18"/><use href="#st" x="36"/><use href="#st" x="54"/><use href="#st" x="72"/></g></svg></div>
  <div class="abs quote" style="left:782px"><p>Nam libero tempore, cum soluta nobis est eligendi optio cumque nihil impedit quo minus id quod maxime placea</p><h4>Owen Brask</h4>
    <svg class="stars" width="90" height="16" viewBox="0 0 90 16"><g fill="#ffd81a"><use href="#st"/><use href="#st" x="18"/><use href="#st" x="36"/><use href="#st" x="54"/><use href="#st" x="72"/></g></svg></div>

  <div class="abs avatar" style="left:222px" role="img" aria-label="Portrait photo of the reviewer"></div>
  <div class="abs avatar" style="left:557px" role="img" aria-label="Portrait photo of the reviewer"></div>
  <div class="abs avatar" style="left:892px" role="img" aria-label="Portrait photo of the reviewer"></div>

  <svg class="abs arrow" style="left:30px" viewBox="0 0 48 48"><path d="M27 16l-8 8 8 8" fill="none" stroke="#fff" stroke-width="2.5"/></svg>
  <svg class="abs arrow" style="left:1124px" viewBox="0 0 48 48"><path d="M21 16l8 8-8 8" fill="none" stroke="#fff" stroke-width="2.5"/></svg>
</section>

<footer>
  <div class="abs social" style="left:487px">Kivo</div>
  <div class="abs social" style="left:545px">Trelo</div>
  <div class="abs social" style="left:603px">Velm</div>
  <div class="abs social" style="left:661px">Pimo</div>

  <div class="abs foot" style="top:3235px">
    <svg width="11" height="15" viewBox="0 0 11 15"><path d="M5.5 0a5.5 5.5 0 015.5 5.5C11 9.5 5.5 15 5.5 15S0 9.5 0 5.5A5.5 5.5 0 015.5 0z" fill="#1b87c9"/><circle cx="5.5" cy="5.5" r="2" fill="#fff"/></svg>Larkhill, ST 40210, United States<span class="sep">|</span><svg width="14" height="14" viewBox="0 0 14 14"><path d="M3 0l3 3-2 2.5a9 9 0 004.5 4.5L11 8l3 3-2.5 3C5 14 0 9 0 2.5z" fill="#1b87c9"/></svg>1 555 010 0142<span class="sep">|</span><svg width="16" height="12" viewBox="0 0 16 12"><rect width="16" height="12" rx="1" fill="#1b87c9"/><path d="M1 1l7 6 7-6" fill="none" stroke="#fff" stroke-width="1.4"/></svg>info@q7vcorp.com
  </div>
  <div class="abs foot" style="top:3273px">Help<span class="sep">|</span>FAQ<span class="sep">|</span>Support<span class="sep">|</span>Sitemap<span class="sep">|</span>Terms Of Use<span class="sep">|</span>Privacy Statement</div>
  <div class="abs foot" style="top:3309px">Q7V Corp © 2018 All rights reserved.</div>
</footer>

</body>
</html>
```